Looking for a modern, Professional business card design

We have a simple business card, but are looking for a more modern, professional look. A sample of the basic card is attached as well as the logo. We would also like to add that we offer:
Struggling with your finances?
- Learn to become debt free
- Discover the power of cash
- Control your money instead of it controlling you
Let us help you achieve a new level of financial freedom!
Also, we would like to have a "SPECIAL OFFER!: FREE 30 minute consultation"
Financial Planning

```html
<!DOCTYPE html>
<html lang="en">
<head>
<meta charset="utf-8">
<title>Harborline Financial Coaching – Business Card</title>
<link href="https://fonts.googleapis.com/css2?family=Oswald:wght@600&family=Questrial&family=Arimo:wght@400;700&display=swap" rel="stylesheet">
<style>
  :root {
    --page-bg: #e4e2df;
    --card-light: #eef0ef;
    --card-light-edge: #d9dcdb;
    --card-dark: #111111;
    --card-dark-soft: #2b2b2b;
    --brand-green: #3f9a2a;
    --brand-green-deep: #1f6e1a;
    --ink: #1a1a1a;
    --muted-light: #c9c9c9;
    --name-green: #2f7a25;
  }
  * { margin: 0; padding: 0; box-sizing: border-box; }
  html, body { width: 1200px; height: 969px; overflow: hidden; }
  body { background: var(--page-bg); position: relative; }

  .business-card {
    position: absolute;
    left: 100px; top: 200px;
    width: 1000px; height: 570px;
    border-radius: 30px;
    overflow: hidden;
    box-shadow: 0 18px 40px rgba(0,0,0,0.25);
  }
  .card-background { position: absolute; inset: 0; width: 100%; height: 100%; }

  .brand-block { position: absolute; left: 60px; top: 95px; }
  .brand-name {
    display: flex; align-items: center; gap: 18px;
    font-family: "Oswald", sans-serif; font-weight: 600;
    font-size: 70px; line-height: 1; color: var(--ink);
    letter-spacing: 1px; text-transform: uppercase;
  }
  .brand-dot {
    width: 58px; height: 58px; border-radius: 50%;
    background: var(--brand-green); flex: none;
  }
  .brand-subline {
    margin-top: 10px; margin-left: 76px;
    font-family: "Oswald", sans-serif; font-weight: 600;
    font-size: 34px; line-height: 1; color: var(--brand-green);
    letter-spacing: 1px; text-transform: uppercase;
  }
  .brand-tagline {
    margin-top: 10px; margin-left: 76px;
    font-family: "Questrial", sans-serif; font-size: 17px; color: var(--ink);
  }

  .offer-badge { position: absolute; left: 848px; top: 40px; width: 130px; height: 130px; }

  .contact-list {
    position: absolute; left: 50px; top: 400px;
    list-style: none;
    font-family: "Arimo", sans-serif; font-size: 25px; color: var(--muted-light);
  }
  .contact-item { display: flex; align-items: center; gap: 18px; height: 42px; }
  .contact-icon { width: 20px; height: 22px; flex: none; }

  .holder { position: absolute; right: 62px; top: 440px; text-align: center; font-family: "Arimo", sans-serif; }
  .holder-name { font-size: 30px; color: var(--name-green); letter-spacing: 1px; }
  .holder-role { margin-top: 8px; font-size: 25px; color: var(--muted-light); }
</style>
</head>
<body>
  <article class="business-card">
    <svg class="card-background" viewBox="0 0 1000 570" preserveAspectRatio="none">
      <defs>
        <linearGradient id="light-face" x1="0" y1="0" x2="0" y2="1">
          <stop offset="0" stop-color="#f6f7f6"/>
          <stop offset="1" stop-color="#dfe2e1"/>
        </linearGradient>
        <linearGradient id="dark-face" x1="0" y1="0" x2="0" y2="1">
          <stop offset="0" stop-color="#2b2b2b"/>
          <stop offset="0.35" stop-color="#111111"/>
          <stop offset="1" stop-color="#1a1a1a"/>
        </linearGradient>
      </defs>
      <rect width="1000" height="570" fill="url(#light-face)"/>
      <path d="M0 330 C 200 320, 380 310, 560 285 C 720 262, 860 250, 1000 270 L1000 300 C 860 285, 700 300, 560 315 C 380 335, 200 345, 0 345 Z" fill="var(--brand-green)"/>
      <path d="M0 345 C 200 345, 380 335, 560 315 C 700 300, 860 285, 1000 300 L1000 570 L0 570 Z" fill="url(#dark-face)"/>
    </svg>

    <div class="brand-block">
      <div class="brand-name"><span class="brand-dot"></span>Harborline</div>
      <div class="brand-subline">Financial Coaching</div>
      <div class="brand-tagline">Achieve a new level of personal freedom</div>
    </div>

    <svg class="offer-badge" viewBox="0 0 130 130" aria-label="Special offer: free 30 minute consultation">
      <defs>
        <path id="badge-ring" d="M65 65 m-50 0 a50 50 0 1 1 100 0 a50 50 0 1 1 -100 0"/>
      </defs>
      <circle cx="65" cy="65" r="63" fill="#1c1c1c"/>
      <circle cx="65" cy="65" r="40" fill="var(--brand-green)" stroke="#8fd16f" stroke-width="3"/>
      <text font-family="Arimo, sans-serif" font-weight="700" font-size="13" fill="var(--brand-green)" letter-spacing="1">
        <textPath href="#badge-ring">FREE 30 MINUTE CONSULTATION</textPath>
      </text>
      <text x="65" y="62" text-anchor="middle" font-family="Arimo, sans-serif" font-weight="700" font-size="12" fill="#ffffff">SPECIAL</text>
      <text x="65" y="77" text-anchor="middle" font-family="Arimo, sans-serif" font-weight="700" font-size="12" fill="#ffffff">OFFER!</text>
    </svg>

    <ul class="contact-list">
      <li class="contact-item">
        <svg class="contact-icon" viewBox="0 0 20 22"><rect x="4" y="1" width="12" height="20" rx="2" fill="none" stroke="var(--brand-green)" stroke-width="2.5"/><circle cx="10" cy="17" r="1.5" fill="var(--brand-green)"/></svg>
        (205) 555-0183
      </li>
      <li class="contact-item">
        <svg class="contact-icon" viewBox="0 0 20 22"><rect x="1" y="5" width="18" height="13" fill="var(--brand-green)"/><path d="M1 5 L10 12 L19 5" fill="none" stroke="#111" stroke-width="1.8"/></svg>
        daniel@steadyledgerplans.com
      </li>
      <li class="contact-item">
        <svg class="contact-icon" viewBox="0 0 20 22"><circle cx="10" cy="11" r="9" fill="var(--brand-green)"/><path d="M1 11 H19 M10 2 C6 6,6 16,10 20 M10 2 C14 6,14 16,10 20" fill="none" stroke="#111" stroke-width="1.3"/></svg>
        www.steadyledgerplans.com
      </li>
    </ul>

    <div class="holder">
      <div class="holder-name">DANIEL R. HAYES</div>
      <div class="holder-role">Personal Financial Coach</div>
    </div>
  </article>
</body>
</html>
```